Bright Ledger Bookkeeping Business Cards

I need Business Cards for a new Bookkeeping Business on the Gold Coast, Australia called "Bright Ledger Bookkeeping". I do Bookkeeping & BAS's for small to medium size businesses onsite (ie I am Mobile) or in house (at my office). I also do one on one Training onsite with clients.
I am a Registered BAS Agent, Accredited Partner with Tallyo & Member of the LEDGRA Bookkeeping Circle. The Logo's I have uploaded all need to be on a white background.

Target Market(s)

Small to Medium Size Businesses

Industry/Entity Type

Business

Contact Information for Business Card

Bright Ledger Bookkeeping
Kim Farrow
PO Box 562 Marlin Reach, Qld 4388
ph 0488 615 903
email kim@kimfarrow-example.com.au

Font styles to use
Other font styles liked:
• Maybe something like Bradley Hand ITC

Requirements
Must have
• All logo's attached on white background.
• Should state that I am a Registered BAS Agent.
Nice to have
• I have a tag - "Bright Ledger - Clear Sums" if you think that works please add.
Should not have
• No brown, green or yellow please.

```html
<!DOCTYPE html>
<html lang="en">
<head>
<meta charset="utf-8">
<title>Bright Ledger Bookkeeping – Business Cards</title>
<link rel="stylesheet" href="https://fonts.googleapis.com/css2?family=Allura&family=Delius&display=swap">
<style>
  :root {
    --backdrop: #2a2a2c;
    --brand-purple: #2d1f6e;
    --brand-purple-light: #3a2a86;
    --card-white: #ffffff;
    --ink: #2b2b2b;
    --rule: #8a8a95;
    --badge-grey: #c4c6ca;
  }
  * { box-sizing: border-box; margin: 0; padding: 0; }
  html, body { width: 1200px; height: 800px; overflow: hidden; }
  body {
    background: var(--backdrop);
    position: relative;
    font-family: "Delius", "Comic Sans MS", sans-serif;
  }
  .card {
    position: absolute;
    top: 248px;
    width: 479px;
    height: 289px;
    box-shadow: 0 6px 18px rgba(0,0,0,0.45);
  }
  .card--front {
    left: 100px;
    background: radial-gradient(ellipse at 45% 40%, var(--brand-purple-light), var(--brand-purple) 70%);
    color: var(--card-white);
  }
  .card--back { left: 623px; background: var(--card-white); color: var(--ink); }

  .brand-name {
    position: absolute;
    text-align: center;
    font-weight: 400;
  }
  .brand-name__main {
    display: block;
    font-family: "Allura", cursive;
    line-height: 0.9;
  }
  .brand-name__sub {
    display: block;
    font-family: "Delius", sans-serif;
    letter-spacing: 1px;
    line-height: 1;
  }
  .card--front .brand-name { left: 0; right: 0; top: 92px; }
  .card--front .brand-name__main { font-size: 66px; }
  .card--front .brand-name__sub { font-size: 24px; margin-top: -2px; padding-left: 40px; }

  .card--back .brand-name { left: 14px; width: 210px; top: 106px; color: var(--brand-purple); }
  .card--back .brand-name__main { font-size: 38px; }
  .card--back .brand-name__sub { font-size: 14px; margin-top: 0; padding-left: 20px; }

  .divider {
    position: absolute; left: 225px; top: 64px; width: 1px; height: 130px; background: var(--rule);
  }
  .contact { position: absolute; left: 236px; top: 62px; white-space: nowrap; }
  .contact__name {
    font-family: "Allura", cursive; font-size: 46px; font-weight: 400; line-height: 1; color: var(--ink);
  }
  .contact__address { font-size: 13px; line-height: 1.2; margin-top: 8px; }
  .contact__lines { font-size: 13px; line-height: 1.2; margin-top: 12px; }
  .contact__label { color: var(--brand-purple); }

  .partners {
    position: absolute; left: 0; right: 0; top: 234px;
    display: flex; align-items: center; justify-content: center; gap: 40px;
    color: var(--brand-purple);
  }
  .partner { display: flex; align-items: center; gap: 6px; font-size: 13px; }
  .partner--bas { font-size: 10px; line-height: 1.1; color: var(--ink); }
  .partner__badge { width: 30px; height: 30px; border-radius: 50%; background: var(--badge-grey); }
</style>
</head>
<body>
  <section class="card card--front" aria-label="Card front">
    <h1 class="brand-name">
      <span class="brand-name__main">Bright Ledger</span>
      <span class="brand-name__sub">Bookkeeping</span>
    </h1>
  </section>

  <section class="card card--back" aria-label="Card back">
    <p class="brand-name">
      <span class="brand-name__main">Bright Ledger</span>
      <span class="brand-name__sub">Bookkeeping</span>
    </p>
    <div class="divider"></div>
    <div class="contact">
      <h2 class="contact__name">Kim Farrow</h2>
      <p class="contact__address">PO Box 562 Marlin Reach,<br>Qld 4388</p>
      <p class="contact__lines">
        <span class="contact__label">ph</span> 0488 615 903<br>
        <span class="contact__label">email</span> kim@kimfarrow-example.com.au
      </p>
    </div>
    <div class="partners">
      <div class="partner partner--bas">
        <span class="partner__badge" role="img" aria-label="Registered practitioner badge"></span>
        <span>BAS agent<br>31750982</span>
      </div>
      <div class="partner"><span>Tallyo</span></div>
      <div class="partner"><span>LEDGRA</span></div>
      <div class="partner"><span>Numbra</span></div>
    </div>
  </section>
</body>
</html>
```